Lotstallmart.com Webpage Design

Design Brief for lotstallmart.com (Copy of Brief also in attached Word file)

Name of Website- lotstallmart.com (existing logo and look & feel of website to be changed)

Logo - Finalised. The logo files are attached with the brief as “logo.jpeg”. The “Blue- Grey” version of the logo is for use on lighter backgrounds and the “Orange-White” version of the logo is for use on darker backgrounds. (A full Black version of the logo is also attached). Both versions may be used in different parts of the website. All attached files are in .png format.
Status - The website in functional and is undergoing user trials. However, we want to improve the look & feel of the website so at it seems
a. cotemporary,
b. Easy to Navigate
c. professional and
d. Vibrant.

Please visit ‘lotstallmart.com’ to check out the website and its functionalities – please use it only as a reference for the features & functions to be provided, however the designer should use a ‘Free Hand’ in designing the composition of various parts of the webpage without getting too influenced by the existing design

Objective of the Website ‘lotstallmart.com –
a. It is a portal focussed on listing of ‘Retail’ specific real-estate properties by developers, owners and realty brokers. The properties shall listed under the following four categories-
i. Retail Malls
ii. Shopping Complexes
iii. High-street shops
iv. Retail Warehouses
*refer lotstallmart.com for better clarity

b. The abovementioned properties shall be listed either for ‘Sale’ or ‘rent\lease’ or both

c. Users shall visit the site in case they wish to acquire a retail \ shop space either on ‘sale’ or ‘rent’. These Users would be able to specify the ‘Search Criteria’ through the tool-bars provided on the website – the ‘Search Criteria’ shall comprise of ‘Type of space category’, ‘City’, ‘Locality’, transaction type ie ‘Rent \ Sale’ and ‘Area Range’

d. The main revenue model for the website shall be listing fee ( or advertising charges ) payable by those listing their properties on the website.

Three Main Pages of Website (lotstallmart.com) that need to be designed -
a. Main Home Page (visit the web link - http://lotstallmart.com/ ) - The main home page has the “Search Toolbar” for specifying of Search Criteria by the User. It shall also have the following features & functions-
i. Main Advertising Banner
ii. Featured Projects
iii. New Launches
iv. Toolbar with buttons – ‘Advertise with Us’, ‘Listings Alert’, ‘Mart Wizards’, ‘Advertiser Login’

b. Property Listings Page (visit the web link - http://lotstallmart.com/gurgaon-in-india ) - The List of property options that match the Criteria specified by the ‘User’ get displayed on this page.

c. Property Detail Page - When the ‘User’ clicks on the “More….” Button on the ‘Property Listings Page’ (given in point b. above) the web page with the details of the property opens. (For Example – visit the web link - http://lotstallmart.com/vorne-Shopping-Complex-vorne-quadrion-gurgaon-636 )

Note:- Please refer to attached ‘Shopping’ related images the designer may use them on the website to provide a look & feel of retail if required – either separately or rotate in a single window

Target Market(s)

Retailers & Investors looking for retail space, Real Estate Brokers, Developers

Industry/Entity Type

Advertising

Number of Pages Required

3 page

Requirements
Must have
• Refer to existing site lotstallmart.com -- all the existing functionalities are a must have.
Nice to have
• The Designer may use the retail related images on the website if required for making it more vibrant. Refer attached images Shopping(1-6).jpg

```html
<!DOCTYPE html>
<html lang="en">
<head>
<meta charset="utf-8">
<title>Lotstallmart.com – India's Leading Portal for Retail Space</title>
<link href="https://fonts.googleapis.com/css2?family=Oswald:wght@400;500;700&family=Open+Sans:wght@400;600;700&display=swap" rel="stylesheet">
<style>
:root{
  --orange:#f7a823;
  --orange-dark:#e08f10;
  --ink:#222;
  --topbar:#2a2a2a;
  --header:#303030;
  --citybar:#262626;
  --section-dark:#3a3a3a;
  --footer:#2d2d2d;
  --card-foot:#8c8c8c;
  --link:#2a86cf;
  --search-blue:#1d8fdc;
  --wizard-panel:#cfe0e6;
  --muted:#b5b5b5;
}
*{box-sizing:border-box;margin:0;padding:0}
html,body{width:1200px;height:2874px;overflow:hidden}
body{font-family:"Open Sans",Arial,sans-serif;color:var(--ink);background:#fff;position:relative}
.wrap{width:880px;margin:0 auto;position:relative}

/* top bar */
.topbar{height:42px;background:var(--topbar);font-size:13px;color:#ddd}
.topbar .wrap{display:flex;align-items:center;height:42px}
.topbar .contact span{color:var(--orange);margin-right:18px}
.topbar .contact b{font-weight:400;color:var(--orange)}
.topbar .acct{margin-left:auto;display:flex;gap:12px}
.acct-btn{background:var(--orange);color:var(--ink);font-size:11px;font-weight:700;padding:0 16px;height:32px;display:flex;align-items:center;gap:8px}
.acct-btn svg{width:12px;height:12px}

/* header */
.header{height:95px;background:var(--header)}
.header .wrap{display:flex;align-items:center;height:95px}
.brand{display:flex;align-items:center;gap:10px}
.brand-dot{width:30px;height:30px;border-radius:50%;background:var(--orange)}
.brand-name{font-size:29px;font-weight:700;color:#fff;line-height:1}
.brand-tag{font-size:8px;color:#ccc;letter-spacing:.5px;margin-top:4px}
.mainnav{margin-left:auto;display:flex;gap:34px}
.mainnav a{text-decoration:none;color:#fff;font-family:"Oswald",sans-serif;font-size:17px;font-weight:500;line-height:1.05;text-transform:uppercase}
.mainnav small{display:block;font-family:"Open Sans",sans-serif;font-size:10px;text-transform:none;color:#ddd;font-weight:400}

.citybar{height:31px;background:var(--citybar)}
.citybar .wrap{display:flex;justify-content:space-between;align-items:center;height:31px;font-size:13px;color:#ddd}

/* hero */
.hero{height:467px;position:relative;background:linear-gradient(110deg,#3b2a1c 0%,#8a6a45 35%,#c79b62 55%,#7c5a3a 80%,#2e2218 100%)}
.hero-photo{position:absolute;inset:0}
.search{position:absolute;left:170px;top:8px;width:265px;height:410px;background:rgba(255,255,255,.93);padding:14px 12px}
.search h3{font-size:12px;font-weight:700;margin-bottom:10px;color:#222;text-transform:uppercase}
.search label{display:block;font-size:10.5px;font-weight:600;margin:10px 0 5px}
.search label a{color:var(--link);text-decoration:none;font-weight:600}
.checks{display:grid;grid-template-columns:1fr 1fr;gap:5px 8px;font-size:10px}
.checks span{display:flex;align-items:center;gap:5px}
.checks i{width:9px;height:9px;border:1px solid #888;background:#fff;display:inline-block}
.field{height:24px;background:#e4e4e4;font-size:10px;color:#888;padding:0 8px;display:flex;align-items:center}
.search-btn{position:absolute;left:0;right:0;bottom:0;height:44px;background:var(--search-blue);color:#fff;font-family:"Oswald",sans-serif;font-size:20px;display:flex;align-items:center;justify-content:center;gap:10px}

/* categories */
.categories{position:absolute;top:594px;left:0;width:1200px;height:140px}
.cat-row{width:830px;margin:0 auto;display:flex;justify-content:space-between}
.cat{width:195px;position:relative;padding-top:32px}
.cat-cap{position:absolute;top:0;left:50%;margin-left:-48px;width:96px;height:50px;border-radius:48px 48px 0 0;background:var(--orange);display:flex;justify-content:center;padding-top:8px}
.cat-cap svg{width:50px;height:36px}
.cat-body{background:var(--orange);height:100px;text-align:center;padding-top:36px;border:3px solid #fff;border-top:none}
.cat-body h4{font-family:"Oswald",sans-serif;font-size:17px;font-weight:700;text-transform:uppercase;line-height:1}
.cat-body p{font-size:11px;margin-top:3px}

/* listings */
.listings{position:absolute;left:0;width:1200px;background:var(--section-dark)}
.listings.featured{top:810px;height:543px}
.listings.launches{top:1430px;height:534px}
.ribbon{position:absolute;left:50%;top:-22px;transform:translateX(-50%);width:310px;height:56px}
.ribbon svg{position:absolute;inset:0}
.ribbon h2{position:relative;text-align:center;font-family:"Oswald",sans-serif;font-weight:500;font-size:27px;line-height:48px;color:#222;text-transform:uppercase}
.ribbon small{position:absolute;top:52px;left:0;right:0;text-align:center;font-size:9px;color:#ddd;letter-spacing:1px}
.grid{position:absolute;left:170px;top:72px;width:866px;display:grid;grid-template-columns:repeat(5,164px);gap:12px 11px}
.card{background:#fff;height:210px;position:relative}
.card-img{height:110px}
.card-city{position:absolute;top:96px;left:0;background:var(--orange);font-family:"Oswald",sans-serif;font-size:13px;font-weight:500;padding:2px 8px;text-transform:uppercase}
.card h5{font-size:12px;font-weight:600;line-height:1.3;padding:22px 8px 0;height:60px}
.card .type{font-size:11px;color:var(--link);padding:6px 8px 0}
.card-foot{position:absolute;bottom:0;left:0;right:0;height:22px;background:var(--card-foot);color:#fff;font-size:9.5px;display:flex;align-items:center;justify-content:space-between;padding:0 8px}
.card-foot i{width:12px;height:12px;border:1px solid #fff;border-radius:50%;display:inline-block}
.g1{background:linear-gradient(180deg,#9cbbd6,#d8c8a8 70%,#8d8d8d)}
.g2{background:linear-gradient(180deg,#1e2a44,#5a4a5c 60%,#d7a25a)}
.g3{background:linear-gradient(180deg,#b9cfe0,#dfe6ea 60%,#a4a9ad)}
.g4{background:linear-gradient(180deg,#1c2238,#6b4a2c 60%,#e3a545)}
.g5{background:linear-gradient(180deg,#b5c7d8,#c9a57c 60%,#8a7a6a)}
.g6{background:linear-gradient(180deg,#8fb0cc,#5c7aa0 60%,#3f4a58)}

/* editor + wizards */
.editor{position:absolute;top:1964px;left:0;width:1200px;height:300px}
.editor-copy{position:absolute;left:170px;top:28px;width:400px}
.editor-copy h2{font-family:"Oswald",sans-serif;font-weight:500;font-size:31px;text-transform:uppercase}
.editor-copy p{font-size:13px;line-height:1.5;margin-top:30px}
.more-btn{display:inline-block;margin-top:22px;background:var(--orange);font-size:12px;font-weight:600;padding:4px 20px}
.wizards{position:absolute;left:612px;top:45px;width:428px;height:215px;background:var(--wizard-panel);padding:14px 14px}
.wizards h3{font-family:"Oswald",sans-serif;font-weight:500;font-size:22px;color:#333;text-transform:uppercase}
.wizards p{font-size:11px;line-height:1.45;margin-top:4px;color:#333}
.wiz-form{display:grid;grid-template-columns:180px 1fr;gap:8px 10px;margin-top:10px}
.wiz-input{height:26px;background:#fff;font-size:10.5px;color:#777;padding:0 8px;display:flex;align-items:center}
.wiz-area{grid-row:1 / span 2;grid-column:2;height:60px;align-items:flex-start;padding-top:6px}
.send-btn{width:180px;height:26px;background:var(--orange-dark);color:#fff;font-size:11px;font-weight:600;display:flex;align-items:center;justify-content:center}

/* footer */
.footer{position:absolute;top:2310px;left:0;width:1200px;height:564px;background:var(--footer);color:#ccc}
.alert{position:absolute;top:2263px;left:162px;width:878px;height:132px;background:var(--orange);text-align:center;padding-top:12px;z-index:2}
.alert h3{font-family:"Oswald",sans-serif;font-weight:500;font-size:19px;text-transform:uppercase}
.alert p{font-size:11px}
.alert-form{display:flex;gap:10px;justify-content:center;margin-top:14px;text-align:left}
.alert-input{height:32px;background:#fff;font-size:11px;color:#777;padding:0 10px;display:flex;align-items:center;position:relative}
.alert-input.sel{padding-right:30px}
.alert-input.sel::after{content:"";position:absolute;right:0;top:0;width:26px;height:32px;background:#ccc}
.alert-input.sel svg{position:absolute;right:8px;top:12px;width:10px;height:8px;z-index:1}
.alert-caption{position:absolute;top:38px;left:0;right:0;font-size:9.5px;text-align:center}
.subscribe{height:32px;width:134px;background:#1a1a1a;color:#fff;font-family:"Oswald",sans-serif;font-size:17px;display:flex;align-items:center;justify-content:center}
.touch{position:absolute;left:170px;top:188px;font-family:"Oswald",sans-serif;font-size:38px;line-height:1;color:#fff;text-transform:uppercase;font-weight:500}
.cols{position:absolute;left:170px;top:292px;width:870px;display:flex;font-size:11px;line-height:1.5}
.cols h4{color:#fff;font-size:12px;font-weight:700;margin-bottom:4px}
.col-contact{width:180px}
.col-visit{width:170px}
.col-social{width:152px;display:flex;gap:5px;padding-top:2px}
.col-social i{width:26px;height:26px;display:block}
.col-about{flex:1}
.col-about a{color:var(--orange);text-decoration:none}
.footlinks{position:absolute;left:170px;top:420px;width:870px;border-top:1px solid #444;border-bottom:1px solid #444;padding:8px 0;font-size:11px;color:#ddd;text-transform:uppercase}
.footlinks span{margin:0 6px}
.copyright{position:absolute;left:0;right:0;bottom:0;height:36px;background:#232323;font-size:9.5px;color:#888;text-align:center;line-height:36px;text-transform:uppercase}
</style>
</head>
<body>

<div class="topbar">
  <div class="wrap">
    <div class="contact"><span>Phone: <b>000-000-0000</b></span><span>Email: <b>info@lotstallmart.com</b></span></div>
    <div class="acct">
      <div class="acct-btn"><svg viewBox="0 0 12 12"><circle cx="6" cy="4" r="3" fill="#222"/><rect x="1" y="8" width="10" height="4" rx="2" fill="#222"/></svg>ADVERTISER REGISTER</div>
      <div class="acct-btn"><svg viewBox="0 0 12 12"><rect x="1" y="5" width="10" height="7" fill="#222"/><path d="M3 5V3a3 3 0 0 1 6 0v2" stroke="#222" stroke-width="1.5" fill="none"/></svg>ADVERTISER LOGIN</div>
    </div>
  </div>
</div>

<header class="header">
  <div class="wrap">
    <div class="brand">
      <span class="brand-dot"></span>
      <div><div class="brand-name">lotstallmart</div><div class="brand-tag">INDIA'S LEADING PORTAL FOR RETAIL SPACE</div></div>
    </div>
    <nav class="mainnav">
      <a href="#">Advertise with us<small>Standard listing - FREE</small></a>
      <a href="#">Mart Wizards<small>Shop Search Services</small></a>
      <a href="#">Listing Alert<small>Email update on New Listings</small></a>
      <a href="#">List your property<small>Click to view Property Listings</small></a>
    </nav>
  </div>
</header>

<div class="citybar">
  <div class="wrap">
    <span>Bangalore</span><span>Chennai</span><span>Greater Noida</span><span>Gurgaon</span><span>Hyderabad</span><span>Jaipur</span><span>Khanna</span><span>Kolkatta</span><span>Mumbai</span><span>Noida</span><span>Pune</span><span>Surat</span>
  </div>
</div>

<section class="hero">
  <div class="hero-photo" role="img" aria-label="Family walking with shopping bags through a lit shopping arcade"></div>
  <form class="search">
    <h3>Search By</h3>
    <label>Select Retail Format : <a href="#">Meaning of Retail Format</a></label>
    <div class="checks">
      <span><i></i>Retail Malls</span><span><i></i>Shopping Complex</span>
      <span><i></i>High Street Shops</span><span><i></i>Retail Warehouses</span>
    </div>
    <label>Sale Or Rent Or Both</label><div class="field">Both</div>
    <label>Select City</label><div class="field">Select</div>
    <label>Select Locality/Micro Market</label><div class="field">Select</div>
    <label>Enter Keywords</label><div class="field">Name of Project, Developers etc</div>
    <div class="search-btn"><svg width="18" height="18" viewBox="0 0 18 18"><circle cx="7" cy="7" r="5" stroke="#fff" stroke-width="2.5" fill="none"/><path d="M11 11l5 5" stroke="#fff" stroke-width="3"/></svg>SEARCH</div>
  </form>
</section>

<div class="categories">
  <div class="cat-row">
    <div class="cat">
      <div class="cat-cap"><svg viewBox="0 0 50 36"><rect x="4" y="14" width="14" height="22" fill="#222"/><rect x="20" y="4" width="14" height="32" fill="#222"/><rect x="36" y="18" width="10" height="18" fill="#222"/></svg></div>
      <div class="cat-body"><h4>Retail Malls</h4><p>Centrally Air Conditioned</p></div>
    </div>
    <div class="cat">
      <div class="cat-cap"><svg viewBox="0 0 50 36"><rect x="6" y="10" width="16" height="26" fill="#222"/><rect x="26" y="2" width="18" height="34" fill="#222"/></svg></div>
      <div class="cat-body"><h4>Shopping Complex</h4><p>Non Air-Conditioned Building</p></div>
    </div>
    <div class="cat">
      <div class="cat-cap"><svg viewBox="0 0 50 36"><rect x="2" y="16" width="12" height="20" fill="#222"/><rect x="16" y="8" width="12" height="28" fill="#222"/><rect x="30" y="12" width="8" height="24" fill="#222"/><rect x="40" y="4" width="8" height="32" fill="#222"/></svg></div>
      <div class="cat-body"><h4>High Street Shops</h4><p>Road Facing Retail</p></div>
    </div>
    <div class="cat">
      <div class="cat-cap"><svg viewBox="0 0 50 36"><path d="M4 14L25 2l21 12v22H4z" fill="#222"/><rect x="16" y="22" width="18" height="14" fill="#f7a823"/></svg></div>
      <div class="cat-body"><h4>Retail Warehouses</h4><p>Back-end Retail Storage</p></div>
    </div>
  </div>
</div>

<section class="listings featured">
  <div class="ribbon">
    <svg viewBox="0 0 310 56" preserveAspectRatio="none"><path d="M0 6h22v44H0l10-22z" fill="#d98e14"/><path d="M310 6h-22v44h22l-10-22z" fill="#d98e14"/><rect x="18" y="0" width="274" height="48" fill="#f7a823"/></svg>
    <h2>Featured Projects</h2><small>ACROSS INDIA</small>
  </div>
  <div class="grid">
    <article class="card"><div class="card-img g1" role="img" aria-label="Mall exterior photo"></div><span class="card-city">Surat</span><h5>Halvern Arcade</h5><div class="type">Shopping Complex</div><div class="card-foot">VIEW THE LISTING<i></i></div></article>
    <article class="card"><div class="card-img g2" role="img" aria-label="High street building at dusk"></div><span class="card-city">Faridabad</span><h5>Tarsel 81 High Street Sector-81</h5><div class="type">Shopping Complex</div><div class="card-foot">VIEW THE LISTING<i></i></div></article>
    <article class="card"><div class="card-img g3" role="img" aria-label="Glass commercial tower"></div><span class="card-city">Gurgaon</span><h5>Q7Q Metroplaza Sector-65</h5><div class="type">Shopping Complex</div><div class="card-foot">VIEW THE LISTING<i></i></div></article>
    <article class="card"><div class="card-img g4" role="img" aria-label="Tower lit at night"></div><span class="card-city">Gurgaon</span><h5>Vexo 24K Sohna Road</h5><div class="type">Retail Malls</div><div class="card-foot">VIEW THE LISTING<i></i></div></article>
    <article class="card"><div class="card-img g5" role="img" aria-label="Mall building with road in front"></div><span class="card-city">New Delhi</span><h5>Corvane Mall-Tagore GardenTagore Garden</h5><div class="type">Retail Malls</div><div class="card-foot">VIEW THE LISTING<i></i></div></article>
    <article class="card"><div class="card-img g1" role="img" aria-label="Mall exterior photo"></div><span class="card-city">Surat</span><h5>Halvern Arcade</h5><div class="type">Shopping Complex</div><div class="card-foot">VIEW THE LISTING<i></i></div></article>
    <article class="card"><div class="card-img g2" role="img" aria-label="High street building at dusk"></div><span class="card-city">Faridabad</span><h5>Tarsel 81 High Street Sector-81</h5><div class="type">Shopping Complex</div><div class="card-foot">VIEW THE LISTING<i></i></div></article>
    <article class="card"><div class="card-img g3" role="img" aria-label="Glass commercial tower"></div><span class="card-city">Gurgaon</span><h5>Q7Q Metroplaza Sector-65</h5><div class="type">Shopping Complex</div><div class="card-foot">VIEW THE LISTING<i></i></div></article>
    <article class="card"><div class="card-img g4" role="img" aria-label="Tower lit at night"></div><span class="card-city">Gurgaon</span><h5>Vexo 24K Sohna Road</h5><div class="type">Retail Malls</div><div class="card-foot">VIEW THE LISTING<i></i></div></article>
    <article class="card"><div class="card-img g5" role="img" aria-label="Mall building with road in front"></div><span class="card-city">New Delhi</span><h5>Corvane Mall-Tagore GardenTagore Garden</h5><div class="type">Retail Malls</div><div class="card-foot">VIEW THE LISTING<i></i></div></article>
  </div>
</section>

<section class="listings launches">
  <div class="ribbon">
    <svg viewBox="0 0 310 56" preserveAspectRatio="none"><path d="M0 6h22v44H0l10-22z" fill="#d98e14"/><path d="M310 6h-22v44h22l-10-22z" fill="#d98e14"/><rect x="18" y="0" width="274" height="48" fill="#f7a823"/></svg>
    <h2>Featured New Launches</h2><small>ACROSS INDIA</small>
  </div>
  <div class="grid">
    <article class="card"><div class="card-img g5" role="img" aria-label="Mall atrium photo"></div><span class="card-city">Bhopal</span><h5>The Grand Bazaar Court Kolar Road</h5><div class="type">Retail Malls</div><div class="card-foot">VIEW THE LISTING<i></i></div></article>
    <article class="card"><div class="card-img g6" role="img" aria-label="Modern commercial building"></div><span class="card-city">Noida</span><h5>Ripple One Sector-18</h5><div class="type">Retail Malls</div><div class="card-foot">VIEW THE LISTING<i></i></div></article>
    <article class="card"><div class="card-img g3" role="img" aria-label="Commercial complex exterior"></div><span class="card-city">Mohali</span><h5>Town Core - SCO In Sector 127 On</h5><div class="type">Retail Malls</div><div class="card-foot">VIEW THE LISTING<i></i></div></article>
    <article class="card"><div class="card-img g2" role="img" aria-label="Shop row at night"></div><span class="card-city">Mohali</span><h5>SCO In Sector 127 On Kharar-Chandigarh</h5><div class="type">Retail Malls</div><div class="card-foot">VIEW THE LISTING<i></i></div></article>
    <article class="card"><div class="card-img g1" role="img" aria-label="Retail building exterior"></div><span class="card-city">Gurgaon</span><h5>The Lazuline Sector 49 Sector 102</h5><div class="type">Shopping Complex</div><div class="card-foot">VIEW THE LISTING<i></i></div></article>
    <article class="card"><div class="card-img g6" role="img" aria-label="Mall exterior at dusk"></div><span class="card-city">New Delhi</span><h5>Kestrel Mall Rohini</h5><div class="type">Retail Malls</div><div class="card-foot">VIEW THE LISTING<i></i></div></article>
    <article class="card"><div class="card-img g3" role="img" aria-label="Glass office and retail block"></div><span class="card-city">Gurgaon</span><h5>Ambrel Triad Dwarka Expressway</h5><div class="type">Shopping Complex</div><div class="card-foot">VIEW THE LISTING<i></i></div></article>
    <article class="card"><div class="card-img g1" role="img" aria-label="Mall building exterior"></div><span class="card-city">Thiruvananthapuram</span><h5>Tall Oak Mall NH Bypass</h5><div class="type">Retail Malls</div><div class="card-foot">VIEW THE LISTING<i></i></div></article>
    <article class="card"><div class="card-img g5" role="img" aria-label="Mall facade"></div><span class="card-city">Mysore</span><h5>Greenlane Mall Hunsur Main Road</h5><div class="type">Retail Malls</div><div class="card-foot">VIEW THE LISTING<i></i></div></article>
    <article class="card"><div class="card-img g6" role="img" aria-label="Large mall complex"></div><span class="card-city">Bangalore</span><h5>Nebula Mall Malleshwaram</h5><div class="type">Retail Malls</div><div class="card-foot">VIEW THE LISTING<i></i></div></article>
  </div>
</section>

<section class="editor">
  <div class="editor-copy">
    <h2>Editor's Choice</h2>
    <p>A "Select" Listing of Retail Properties Handpicked by our Editors based on their own positive evaluation on parameters &amp; attributes such as Design Concept, Location, Developer, Success Potential. So Read On to Check Out for yourself ..............</p>
    <span class="more-btn">More</span>
  </div>
  <div class="wizards">
    <h3>Mart Wizards</h3>
    <p>Post your Retail Space requirement with us &amp; our experts shall get back with suitable options &amp; even help you in your transaction. This is a Free Service!</p>
    <div class="wiz-form">
      <div class="wiz-input">Enter your email address</div>
      <div class="wiz-input wiz-area">Description of Requirement</div>
      <div class="wiz-input">Mobile</div>
      <div class="send-btn">Send</div>
    </div>
  </div>
</section>

<div class="alert">
  <h3>Listing Alert</h3>
  <p>Suscribe for Fortnightly Email update on New Listings @ Lotstallmart</p>
  <div class="alert-form">
    <div class="alert-input" style="width:225px">Enter your email address</div>
    <div class="alert-input sel" style="width:220px">Select options<svg viewBox="0 0 10 8"><path d="M0 0h10L5 8z" fill="#333"/></svg><span class="alert-caption">(select retail format of interest)</span></div>
    <div class="alert-input sel" style="width:220px">Allabad<svg viewBox="0 0 10 8"><path d="M0 0h10L5 8z" fill="#333"/></svg><span class="alert-caption">(select cities of interest)</span></div>
    <div class="subscribe">SUBSCRIBE</div>
  </div>
</div>

<footer class="footer">
  <h2 class="touch">Get in touch<br>with us</h2>
  <div class="cols">
    <div class="col-contact"><h4>Contact Us</h4>info@lotstallmart.com<br>Phone : 000-000-0000<br>Fax : 000 - 000 - 0000</div>
    <div class="col-visit"><h4>Visit Us</h4>Stall Square<br>Unit 406, 4th Floor,<br>Lorem Ipsum is simply,<br>Sector xx, Gurgaon - 122002</div>
    <div class="col-social"><i style="background:#3b5998"></i><i style="background:#2fa9e0"></i><i style="background:#d34836"></i></div>
    <div class="col-about"><h4>About Us</h4>Lotstallmart.com - About Us Lotstallmart.com is a Specialised Web-based platform for Retail Space, featuring properties across India under various formats such as Retail Malls, Shopping Complexes, High-street Shops. Also featured are Retail Warehouses which provide the logistic back end for the retail business. Lotstallmart.com is useful to various category of users as follows: a. Devel <a href="#">More...</a></div>
  </div>
  <div class="footlinks">About Us<span>/</span>Contact Us<span>/</span>Site Map<span>/</span>Retail Malls<span>/</span>Shopping Complex<span>/</span>High Street Shops<span>/</span>Retail Warehouses</div>
  <div class="copyright">Copyright ©2015 Stall Square. All Rights Reserved &nbsp;|&nbsp; Privacy Policy &nbsp;|&nbsp; Terms of Use</div>
</footer>

</body>
</html>
```